Contemporary new French wine brand needs logo and series of label design

to design a new contemporary logo and series of labels for a new French wine brand. We hope to attract not just current French wine drinkers but new ones who may appreciate a less traditional and more modern style.
Updates

Reason: we are wanting to extend the project for a few days more to receive more submissions since we had fewer designs submitted than we were expecting, maybe because of the holidays.

Target Market(s)

people who follow the arts community (eg. music, theatre, visual/video arts, dance) --- all mature ages.

Industry/Entity Type

French Wine

Requirements
Must have
• a clear, memorable treatment for the name MORIVAL with accompanying logo.
Nice to have
• embossing, matte/gloss refinement, tasteful foil stamping, coated stock for the whites to help the integrity of the paper in and out of ice buckets. A combo of say, three types of fonts; a semi custom font for the brand name Morival and maybe a script and one other.
Should not have
• not traditional French

```html
<!DOCTYPE html>
<html lang="fr">
<head>
<meta charset="utf-8">
<title>Morival — label concept</title>
<link rel="stylesheet" href="https://fonts.googleapis.com/css2?family=Open+Sans:wght@400&family=Italianno&family=Cormorant+Garamond:wght@400&display=swap">
<style>
  :root {
    --ink: #1b1b1b;
    --paper: #ffffff;
  }
  html, body {
    margin: 0;
    padding: 0;
    width: 1200px;
    height: 900px;
    overflow: hidden;
    background: var(--paper);
  }
  .canvas { display: block; width: 1200px; height: 900px; }
  .band-light { fill: var(--paper); }
  .band-dark { fill: var(--ink); }
  .wordmark { font-family: "Open Sans", sans-serif; font-size: 40px; letter-spacing: -0.5px; }
  .varietal { font-family: "Italianno", cursive; font-size: 17px; letter-spacing: 5px; }
  .region { font-family: "Cormorant Garamond", serif; font-size: 12px; }

  .label--light .frame { fill: none; stroke: var(--ink); stroke-width: 3; }
  .label--light .frame-inner { fill: none; stroke: var(--paper); stroke-width: 3; }
  .label--light .block { fill: var(--ink); }
  .label--light .mark,
  .label--light .wordmark { fill: var(--ink); }
  .label--light .varietal,
  .label--light .region { fill: var(--paper); }

  .label--dark .frame { fill: none; stroke: var(--paper); stroke-width: 3; }
  .label--dark .frame-inner { fill: none; stroke: var(--ink); stroke-width: 3; }
  .label--dark .block { fill: var(--paper); }
  .label--dark .mark,
  .label--dark .wordmark { fill: var(--paper); }
  .label--dark .varietal,
  .label--dark .region { fill: var(--ink); }
</style>
</head>
<body>
<svg class="canvas" viewBox="0 0 1200 900" xmlns="http://www.w3.org/2000/svg">
  <defs>
    <clipPath id="block-area">
      <rect x="458" y="221" width="283" height="127"/>
    </clipPath>
  </defs>

  <rect class="band-light" x="0" y="0" width="1200" height="450"/>
  <rect class="band-dark" x="0" y="450" width="1200" height="450"/>

  <g class="label label--light">
    <rect class="frame" x="469.5" y="102.5" width="261" height="237"/>
    <rect class="block" x="458" y="221" width="283" height="127"/>
    <rect class="frame-inner" x="469.5" y="102.5" width="261" height="237" clip-path="url(#block-area)"/>
    <rect class="mark" x="590" y="131" width="20" height="20"/>
    <text class="wordmark" x="600" y="220" text-anchor="middle">Morival</text>
    <text class="varietal" x="600" y="285" text-anchor="middle">Sauvignon Blanc</text>
    <text class="region" x="600" y="328" text-anchor="middle">val de loire</text>
  </g>

  <g class="label label--dark" transform="translate(0 450)">
    <rect class="frame" x="469.5" y="102.5" width="261" height="237"/>
    <rect class="block" x="458" y="221" width="283" height="127"/>
    <rect class="frame-inner" x="469.5" y="102.5" width="261" height="237" clip-path="url(#block-area)"/>
    <rect class="mark" x="590" y="131" width="20" height="20"/>
    <text class="wordmark" x="600" y="220" text-anchor="middle">Morival</text>
    <text class="varietal" x="600" y="285" text-anchor="middle">Sauvignon Blanc</text>
    <text class="region" x="600" y="328" text-anchor="middle">val de loire</text>
  </g>
</svg>
</body>
</html>
```